Velmori Sciences needs high end Label Design for a revolutionary new supplement

We at Velmori Sciences are looking for a brand new Label Design for a first of its kind product called Solvenna. It is the first supplement on the market that treats grief and heartbreak. This product is unisex for both men and woman. We want the New Label to look high end and luxurious using the brand colors which are gold and burgundy. Please feel free to use other colors such as black, white, or gray to go along with it or any other colors if you feel would be a great fit! Velmori Sciences is like the Tarnwick of the supplement world, coming out with new products that will challenge the way people treat different symptoms. To Recap:

1. Product Name: SOLVENNA - the font will play a big roll
2. The Label will be placed on an all white bottle
3. Some parts of the label will be printed with foil to make parts of the label shiny and more attractive. Please keep this in mind when designing.
4. Must use our Logo. I will attach a file of our logo and of the emblem as well. Feel free to use the emblem separately if you have a great idea for it. Please let us know if you need the Logo in a different file type.
5. This all natural herbal supplement in pill form is the first to treat grief and support someone with a broken heart. The consumers purchasing this product will be going through a hard and emotional time. This is a serious product.
6. The manufacturer has included some basic instructions regarding the dye line and file types. Please do your best to meet these. If you cannot meet the guidelines please submit art work anyways. If your design is chosen we will just have the manufacturer replicate the design.

The final label should portray Solvenna and Velmori Sciences as a luxurious brand and product which was made with cutting edge science leading the way with revolutionary ideas. We want customers to feel that the product is worth every penny, because it is. As soon as they receive the product and take one look at the label, I want them to think WOW I made the right choice buying this. I have attached some Label designs that we really liked for your review.

Please feel free to message me with any questions or if you need the Logo in a different file type. Thank you all.
Updates

Please send in more entries while we take a couple days to review, we are still looking for that one design we can work with. We are getting close, thank you all!

Target Market(s)

People going through grief and heartbreak.

Font styles to use
Sans Serif
Script
Other font styles liked:
• Any font that looks good, The font for the name SOLVENNA is very important and will brand it. We hated the font used in the label we received in our first label draft (attached so you can see)

Requirements
Must have
• Must have the company Logo that says the company name
• Must have the colors Gold and Burgundy
• Must have some areas that will be the shiny foil when label is printed.
• Must say "Dietary Supplement" somewhere near the bottom along with "90 Capsules"
• I have attached a Label someone designed for us but were not really happy with. I did like the font the "Dietary supplement" and "90 Capsules" had and also where it was placed. We absolutely HATED the font used for Solvenna.
• Must look at the label design we received from the manufacturer and take into consideration the room needed to write in the directions and all the symbols such as "made in america" and "KMT Facility" Don't worry about adding these in as they will put those in before printing but keep in mind they will be added to the Final Label along with the Supplement Facts.
Nice to have
• Would like to see other colors to go with gold and burgundy suck as black, white, or gray. I have attached some Label designs that I really liked for your reference.
Should not have
• Does not need to have any other legal language, that will be applied by the the manufacturer's graphics team.

```html
<!DOCTYPE html>
<html lang="en">
<head>
<meta charset="utf-8">
<title>Solvenna Label – Velmori Sciences</title>
<link rel="stylesheet" href="https://fonts.googleapis.com/css2?family=Josefin+Sans:wght@300&family=Montserrat:wght@400;700&display=swap">
<style>
  :root {
    --backdrop: #f4f3f2;
    --label-light: #f6f5f4;
    --label-mid: #e4e2e1;
    --burgundy-deep: #4a0d1c;
    --burgundy: #6e1428;
    --burgundy-soft: #8f2a3e;
    --gold-dark: #a8803a;
    --gold: #d4af5f;
    --gold-light: #f3dfa2;
  }
  html, body {
    margin: 0;
    padding: 0;
    width: 1200px;
    height: 1200px;
    overflow: hidden;
    background: var(--backdrop);
  }
  .canvas {
    position: relative;
    width: 1200px;
    height: 1200px;
  }
  .label {
    position: absolute;
    left: 45px;
    top: 105px;
    width: 1110px;
    height: 990px;
    box-shadow: 0 6px 24px rgba(0,0,0,0.08);
  }
  .brand-name {
    font-family: "Montserrat", sans-serif;
    font-weight: 700;
  }
  .product-name {
    font-family: "Josefin Sans", sans-serif;
    font-weight: 300;
  }
  .supplement-line {
    font-family: "Montserrat", sans-serif;
    font-weight: 400;
  }
  .capsule-count {
    font-family: "Montserrat", sans-serif;
    font-weight: 700;
  }
</style>
</head>
<body>
<div class="canvas">
  <svg class="label" viewBox="0 0 1110 990" xmlns="http://www.w3.org/2000/svg" aria-label="Solvenna dietary supplement label">
    <defs>
      <linearGradient id="label-surface" x1="0" y1="0" x2="1" y2="1">
        <stop offset="0" stop-color="var(--label-light)"/>
        <stop offset="0.6" stop-color="#efedec"/>
        <stop offset="1" stop-color="var(--label-mid)"/>
      </linearGradient>
      <linearGradient id="wave-band" x1="0" y1="0" x2="1" y2="0">
        <stop offset="0" stop-color="var(--burgundy-deep)"/>
        <stop offset="0.5" stop-color="var(--burgundy)"/>
        <stop offset="1" stop-color="var(--burgundy-soft)"/>
      </linearGradient>
      <linearGradient id="gold-foil" x1="0" y1="0" x2="1" y2="1">
        <stop offset="0" stop-color="var(--gold-dark)"/>
        <stop offset="0.35" stop-color="var(--gold-light)"/>
        <stop offset="0.6" stop-color="var(--gold)"/>
        <stop offset="0.85" stop-color="var(--gold-light)"/>
        <stop offset="1" stop-color="var(--gold-dark)"/>
      </linearGradient>
    </defs>

    <rect class="label-surface" x="0" y="0" width="1110" height="990" fill="url(#label-surface)"/>

    <path class="wave-band" role="img" aria-label="Flowing burgundy wave band with fine foil lines"
          d="M0 556 C 350 545, 750 535, 1110 528 L 1110 790 C 800 880, 400 930, 0 945 Z"
          fill="url(#wave-band)"/>
    <path class="foil-edge" d="M0 556 C 350 545, 750 535, 1110 528" fill="none" stroke="url(#gold-foil)" stroke-width="4"/>
    <path class="foil-edge" d="M1110 790 C 800 880, 400 930, 0 945" fill="none" stroke="url(#gold-foil)" stroke-width="4"/>

    <g class="brand-logo">
      <circle cx="571" cy="168" r="34" fill="url(#gold-foil)"/>
      <text class="brand-name" x="571" y="263" font-size="36" text-anchor="middle" textLength="215" lengthAdjust="spacingAndGlyphs" fill="var(--burgundy)">VELMORI</text>
      <text class="brand-name" x="571" y="288" font-size="20" text-anchor="middle" textLength="190" lengthAdjust="spacingAndGlyphs" fill="var(--burgundy)">SCIENCES</text>
    </g>

    <text class="product-name" x="108" y="694" font-size="190" textLength="873" lengthAdjust="spacingAndGlyphs" fill="url(#gold-foil)">SOLVENNA</text>

    <g class="product-details" fill="url(#gold-foil)">
      <text class="supplement-line" x="453" y="812" font-size="23" textLength="118" lengthAdjust="spacingAndGlyphs">DIETARY</text>
      <text class="supplement-line" x="453" y="849" font-size="23" textLength="172" lengthAdjust="spacingAndGlyphs">SUPPLEMENT</text>
      <text class="capsule-count" x="453" y="896" font-size="42" textLength="66" lengthAdjust="spacingAndGlyphs">90</text>
      <text class="supplement-line" x="531" y="893" font-size="13" textLength="90" lengthAdjust="spacingAndGlyphs">CAPSULES</text>
    </g>
  </svg>
</div>
</body>
</html>
```